VORTAL MED -DIAGNOSTIC CENTRE FOR IMAGES

Our Activity provides diagnostic services for images (RMI, Tac, RX, Ultrasound etc.)
We would like to create a broschure that illustrates our services.
We would like to give maximum attention to the Diagnostic service dedicated to "HEART", therefore maximum evidence to the world of Cardiology.
In the background we would like to highlight the other diagnostic services dedicated to the Rest of the Body (Brain, Knees Legs etc.)
Target Market(s)
PERSONS WHO NEED TO PERFORM DIAGNOSTIC TESTS (MRI, CT, ULTRASOUND, RX ETC.)
Industry/Entity Type
HEALTH
Requirements
Must have
- The company logo, must have diagnostic images (MRI, CT, X-ray, ultrasound), must be simple and intuitive, which is harmonious with the colors of our company logo
Should not have
- Colours that are not in harmony with our company logo

```html
<!DOCTYPE html>
<html lang="en">
<head>
<meta charset="utf-8">
<title>Vortal Med – Diagnostic Brochure Cover</title>
<link rel="stylesheet" href="https://fonts.googleapis.com/css2?family=Montserrat:wght@400;600;700;800&display=swap">
<style>
  :root {
    --brand-blue: #2f6fb8;
    --brand-blue-dark: #1e4f8e;
    --brand-teal: #1fb3a3;
    --brand-green: #5cc99a;
    --paper: #ffffff;
    --text-on-blue: #ffffff;
    --photo-light: #e7edf3;
    --photo-mid: #b9c6d3;
  }
  * { box-sizing: border-box; margin: 0; padding: 0; }
  html, body { width: 843px; height: 1200px; overflow: hidden; background: var(--paper); }
  body { font-family: "Montserrat", sans-serif; }

  .cover { position: relative; width: 843px; height: 1200px; overflow: hidden; background: var(--paper); }

  .scanner-photo {
    position: absolute; left: 0; top: 560px; width: 843px; height: 640px;
    background: linear-gradient(160deg, var(--photo-light) 0%, var(--photo-mid) 60%, #8fa2b6 100%);
  }
  .cover-shapes { position: absolute; inset: 0; }

  .brand {
    position: absolute; left: 60px; top: 62px;
    display: flex; align-items: center; gap: 14px;
  }
  .brand-dot { width: 22px; height: 22px; border-radius: 50%; background: var(--brand-teal); }
  .brand-name { font-weight: 800; font-size: 50px; color: var(--brand-blue); letter-spacing: 1px; }

  .headline {
    position: absolute; left: 60px; top: 215px; width: 520px;
    color: var(--text-on-blue); font-weight: 800; font-size: 46px; line-height: 1.12;
    text-transform: uppercase;
  }
  .services {
    position: absolute; left: 60px; top: 405px; width: 440px;
    color: var(--text-on-blue); font-weight: 700; font-size: 24px; line-height: 1.25;
    text-transform: uppercase;
  }
  .more-info {
    position: absolute; left: 60px; top: 490px;
    background: var(--brand-teal); color: var(--text-on-blue);
    font-weight: 700; font-size: 16px; letter-spacing: 1px;
    padding: 10px 26px; border-radius: 20px;
  }
  .contacts { position: absolute; left: 60px; top: 555px; list-style: none; }
  .contacts li {
    display: flex; align-items: center; gap: 12px;
    color: var(--text-on-blue); font-size: 17px; font-weight: 600; margin-bottom: 12px;
  }
  .contact-icon {
    width: 30px; height: 30px; border-radius: 50%; background: var(--paper);
    display: flex; align-items: center; justify-content: center;
  }

  .machine-photo {
    position: absolute; left: 510px; top: 360px; width: 360px; height: 360px;
    border-radius: 50%; border: 12px solid var(--paper);
    background: radial-gradient(circle at 40% 40%, #f4f7fa 0%, #cfd9e3 55%, #8da3b8 100%);
    box-shadow: 0 0 0 8px var(--brand-teal);
  }
</style>
</head>
<body>
<main class="cover">
  <div class="scanner-photo" role="img" aria-label="Photo of an MRI scanner in a bright examination room"></div>

  <svg class="cover-shapes" width="843" height="1200" viewBox="0 0 843 1200" aria-hidden="true">
    <path d="M0,160 H843 V620 Q560,660 340,860 T0,1140 Z" fill="var(--brand-blue)"/>
    <path d="M843,620 Q560,660 340,860 T0,1140" fill="none" stroke="var(--brand-teal)" stroke-width="22"/>
    <path d="M843,650 Q580,690 370,885 T0,1172" fill="none" stroke="var(--brand-green)" stroke-width="8"/>
    <rect x="0" y="150" width="843" height="10" fill="var(--brand-teal)"/>
  </svg>

  <div class="brand">
    <span class="brand-dot"></span>
    <span class="brand-name">VORTAL MED</span>
  </div>

  <h1 class="headline">Expert diagnosis at the heart of your health.</h1>
  <p class="services">Diagnostic tests (MRI, CT, Ultrasound, RX etc.)</p>
  <span class="more-info">MORE INFO</span>

  <ul class="contacts">
    <li>
      <span class="contact-icon">
        <svg width="16" height="16" viewBox="0 0 24 24"><path d="M6.6 10.8a15 15 0 0 0 6.6 6.6l2.2-2.2a1 1 0 0 1 1-.25 11.4 11.4 0 0 0 3.6.57 1 1 0 0 1 1 1V20a1 1 0 0 1-1 1A17 17 0 0 1 3 4a1 1 0 0 1 1-1h3.5a1 1 0 0 1 1 1c0 1.25.2 2.45.57 3.57a1 1 0 0 1-.25 1z" fill="var(--brand-blue)"/></svg>
      </span>
      +39 012 345 6789
    </li>
    <li>
      <span class="contact-icon">
        <svg width="16" height="16" viewBox="0 0 24 24"><rect x="3" y="5" width="18" height="14" rx="2" fill="none" stroke="var(--brand-blue)" stroke-width="2"/><path d="M3 7l9 6 9-6" fill="none" stroke="var(--brand-blue)" stroke-width="2"/></svg>
      </span>
      info@vortalmed.com
    </li>
    <li>
      <span class="contact-icon">
        <svg width="16" height="16" viewBox="0 0 24 24"><circle cx="12" cy="12" r="9" fill="none" stroke="var(--brand-blue)" stroke-width="2"/><path d="M3 12h18M12 3c3 3 3 15 0 18M12 3c-3 3-3 15 0 18" fill="none" stroke="var(--brand-blue)" stroke-width="2"/></svg>
      </span>
      www.vortalmed.com
    </li>
  </ul>

  <div class="machine-photo" role="img" aria-label="Photo of a CT scanner with patient table"></div>
</main>
</body>
</html>
```